design a construction company business card

Design business card around our logo. Card must have all the typical info: name, title, address, phone, email, business name, etc. Somewhere on the card I would like to see our motto "Grounded in trust... Driven by dedication." Consider adding a splash of bright orange to the card to complement the blues and silvers/grays in the logo. We are open to metallic inks, textures, etc. We would like to see options on both light and dark backgrounds. The font in the logo is Euro Technic Extended Regular.

```html
<!DOCTYPE html>
<html lang="en">
<head>
<meta charset="utf-8">
<title>Halden Contracting – Business Card</title>
<link rel="stylesheet" href="https://fonts.googleapis.com/css2?family=Michroma&family=Roboto:wght@400;700&display=swap">
<style>
  :root{
    --page:#e9ebee;
    --card:#ffffff;
    --blue-deep:#1c4fa8;
    --blue-mid:#1f6fc4;
    --blue-light:#2a93d4;
    --silver:#c9ccd1;
    --silver-light:#e2e4e7;
    --ink-grey:#7d8188;
    --white:#ffffff;
  }
  html,body{margin:0;padding:0;overflow:hidden}
  body{width:1200px;height:780px;background:var(--page);position:relative;font-family:"Roboto",sans-serif}
  .card{position:absolute;top:235px;width:540px;height:309px;border-radius:18px;background:var(--card);overflow:hidden;box-shadow:0 6px 18px rgba(0,0,0,.18)}
  .card--front{left:40px}
  .card--back{left:620px}
  .card__art{position:absolute;inset:0;width:540px;height:309px}

  .brand{position:absolute;font-family:"Michroma",sans-serif;color:var(--blue-mid);font-weight:400}
  .brand__square{display:inline-block;width:16px;height:16px;background:var(--blue-mid);margin-right:10px;vertical-align:middle}
  .brand__name{font-size:34px;letter-spacing:2px;line-height:1;vertical-align:middle}
  .brand__sub{display:block;font-size:12.5px;letter-spacing:2px;margin-top:8px}

  .card--front .brand{left:36px;top:88px}
  .card--back .brand{left:0;right:0;top:118px;text-align:center}
  .card--back .brand__name{font-size:40px}
  .card--back .brand__sub{font-size:14px}

  .contact{position:absolute;left:318px;top:26px;color:var(--ink-grey);font-size:11.5px;line-height:1.55}
  .contact__name{font-family:"Michroma",sans-serif;color:var(--blue-mid);font-size:14px;letter-spacing:1px;margin:0}
  .contact__title{margin:0 0 10px;font-size:12px}
  .contact__line{margin:0;display:flex;align-items:center;gap:8px}
  .contact__icon{width:14px;height:14px;flex:none}
  .contact__spacer{width:14px;flex:none}

  .motto{font-family:"Roboto",sans-serif;font-weight:700;font-size:12.5px;fill:var(--white);letter-spacing:.3px}
  .web{position:absolute;left:0;right:0;bottom:16px;text-align:center;color:var(--white);font-weight:700;font-size:13px;letter-spacing:.5px}
</style>
</head>
<body>

<section class="card card--front" aria-label="Business card front">
  <svg class="card__art" viewBox="0 0 540 309" aria-hidden="true">
    <defs>
      <linearGradient id="bandFront" x1="0" y1="1" x2="1" y2="0">
        <stop offset="0" stop-color="#2a93d4"/>
        <stop offset="1" stop-color="#1c4fa8"/>
      </linearGradient>
      <path id="mottoPath" d="M262,296 Q400,268 532,196"/>
    </defs>
    <path d="M70,309 Q330,272 540,132 L540,160 Q340,290 130,309 Z" fill="#d7dadf"/>
    <path d="M130,309 Q340,290 540,160 L540,309 Z" fill="url(#bandFront)"/>
    <text class="motto"><textPath href="#mottoPath">Grounded in trust... Driven by dedication.</textPath></text>
  </svg>

  <div class="brand">
    <span class="brand__square"></span><span class="brand__name">HALDEN</span>
    <span class="brand__sub">— CONTRACTING, INC. —</span>
  </div>

  <div class="contact">
    <p class="contact__name">MARA QUINLAN</p>
    <p class="contact__title">Founder</p>
    <p class="contact__line"><span class="contact__spacer"></span>PO Box 48 Harbour Lane</p>
    <p class="contact__line"><span class="contact__spacer"></span>7 Wattle Road, Geelong</p>
    <p class="contact__line">
      <svg class="contact__icon" viewBox="0 0 14 14"><circle cx="7" cy="7" r="7" fill="#1f6fc4"/><path d="M4.5 3.5h1.6l.7 2-1 .8a5 5 0 0 0 2 2l.8-1 2 .7v1.6c0 .4-.3.7-.7.7A6.3 6.3 0 0 1 3.8 4.2c0-.4.3-.7.7-.7z" fill="#fff"/></svg>
      555 210 4478</p>
    <p class="contact__line">
      <svg class="contact__icon" viewBox="0 0 14 14"><circle cx="7" cy="7" r="7" fill="#1f6fc4"/><rect x="3.5" y="4.5" width="7" height="5" fill="none" stroke="#fff" stroke-width="1"/><path d="M3.5 4.5 7 7.3l3.5-2.8" fill="none" stroke="#fff" stroke-width="1"/></svg>
      info@haldenbuild.com</p>
    <p class="contact__line">
      <svg class="contact__icon" viewBox="0 0 14 14"><circle cx="7" cy="7" r="7" fill="#1f6fc4"/><circle cx="7" cy="7" r="3.6" fill="none" stroke="#fff" stroke-width="1"/><path d="M3.4 7h7.2M7 3.4c-1.6 2-1.6 5.2 0 7.2M7 3.4c1.6 2 1.6 5.2 0 7.2" fill="none" stroke="#fff" stroke-width=".8"/></svg>
      www.haldenbuild.com</p>
  </div>
</section>

<section class="card card--back" aria-label="Business card back">
  <svg class="card__art" viewBox="0 0 540 309" aria-hidden="true">
    <defs>
      <linearGradient id="bandBack" x1="0" y1="0" x2="1" y2="0">
        <stop offset="0" stop-color="#1c4fa8"/>
        <stop offset=".5" stop-color="#2a93d4"/>
        <stop offset="1" stop-color="#1c4fa8"/>
      </linearGradient>
    </defs>
    <path d="M0,0 H540 V88 Q270,52 0,70 Z" fill="#d7dadf"/>
    <path d="M0,0 H540 V62 Q270,28 0,48 Z" fill="url(#bandBack)"/>
    <path d="M0,309 V232 Q270,258 540,226 V309 Z" fill="#d7dadf"/>
    <path d="M0,309 V254 Q270,280 540,248 V309 Z" fill="url(#bandBack)"/>
  </svg>

  <div class="brand">
    <span class="brand__square"></span><span class="brand__name">HALDEN</span>
    <span class="brand__sub">— CONTRACTING, INC. —</span>
  </div>

  <p class="web">www.haldenbuild.com</p>
</section>

</body>
</html>
```